Rollers & Glides.com

Vertical Business Card with focus on branding with our icon. Information on card will be logo, persons name, position, phone number, email address and website. Use the the name Marcus Pellow, position President, phone number 480.915.2267, email Marcus@rollersandglides-demo.com, website www.rollersandglides-demo.com.

```html
<!DOCTYPE html>
<html lang="en">
<head>
<meta charset="utf-8">
<title>Rollers &amp; Glides.com — Business Card</title>
<link rel="stylesheet" href="https://fonts.googleapis.com/css2?family=Montserrat:wght@700&family=Roboto:wght@400;500&display=swap">
<style>
  :root {
    --brand-blue: #3160ad;
    --ink: #1c1c1c;
    --paper: #ffffff;
    --rule: #8a8a8a;
    --backdrop: #2a2a2a;
  }
  * { box-sizing: border-box; margin: 0; padding: 0; }
  html, body {
    width: 1200px;
    height: 1040px;
    overflow: hidden;
    background: var(--backdrop);
  }
  .canvas {
    position: relative;
    width: 1200px;
    height: 1040px;
  }
  .card {
    position: absolute;
    left: 190px;
    width: 820px;
    height: 450px;
  }
  .card--front {
    top: 50px;
    background: var(--brand-blue);
    border-radius: 90px 0 90px 0;
    display: flex;
    align-items: center;
    justify-content: center;
  }
  .front-name {
    font-family: "Roboto", sans-serif;
    font-weight: 500;
    font-size: 52px;
    color: var(--paper);
    letter-spacing: 1px;
  }
  .card--back {
    top: 540px;
    background: var(--paper);
    border-radius: 0 90px 0 90px;
    display: flex;
    align-items: center;
  }
  .back-brand {
    width: 380px;
    text-align: center;
    font-family: "Roboto", sans-serif;
    font-weight: 500;
    font-size: 31px;
    color: var(--brand-blue);
    letter-spacing: 1px;
  }
  .divider {
    width: 1px;
    height: 220px;
    background: var(--rule);
  }
  .details {
    padding-left: 34px;
    font-family: "Roboto", sans-serif;
    color: var(--ink);
  }
  .person-name {
    font-family: "Montserrat", sans-serif;
    font-weight: 700;
    font-size: 30px;
    color: var(--brand-blue);
    letter-spacing: 0.5px;
    line-height: 1.05;
  }
  .person-role {
    font-size: 24px;
    margin-bottom: 36px;
  }
  .contact-list { list-style: none; }
  .contact-item {
    display: flex;
    align-items: center;
    gap: 12px;
    font-size: 24px;
    line-height: 1.35;
  }
  .contact-icon {
    width: 22px;
    height: 22px;
    flex: none;
    fill: none;
    stroke: var(--brand-blue);
    stroke-width: 2;
  }
  .contact-icon--solid { fill: var(--brand-blue); stroke: none; }
  .web-domain { color: var(--brand-blue); }
</style>
</head>
<body>
<main class="canvas">
  <section class="card card--front" aria-label="Card front">
    <p class="front-name">Rollers &amp; Glides.com</p>
  </section>

  <section class="card card--back" aria-label="Card back">
    <p class="back-brand">Rollers &amp; Glides.com</p>
    <div class="divider"></div>
    <div class="details">
      <h1 class="person-name">MARCUS PELLOW</h1>
      <p class="person-role">President</p>
      <ul class="contact-list">
        <li class="contact-item">
          <svg class="contact-icon contact-icon--solid" viewBox="0 0 24 24" aria-hidden="true">
            <path d="M6.6 10.8a15.1 15.1 0 0 0 6.6 6.6l2.2-2.2c.3-.3.7-.4 1-.2 1.1.4 2.3.6 3.6.6.6 0 1 .4 1 1V20c0 .6-.4 1-1 1A17 17 0 0 1 3 4c0-.6.4-1 1-1h3.5c.6 0 1 .4 1 1 0 1.3.2 2.5.6 3.6.1.3 0 .7-.2 1z"/>
          </svg>
          <span>480.915.2267</span>
        </li>
        <li class="contact-item">
          <svg class="contact-icon contact-icon--solid" viewBox="0 0 24 24" aria-hidden="true">
            <path d="M2 5h20v14H2z M2 5l10 8 10-8" />
            <path d="M2 5l10 8 10-8" fill="none" stroke="#fff" stroke-width="1.6"/>
          </svg>
          <span>Marcus@rollersandglides-demo.com</span>
        </li>
        <li class="contact-item">
          <svg class="contact-icon" viewBox="0 0 24 24" aria-hidden="true">
            <circle cx="12" cy="12" r="9.5"/>
            <ellipse cx="12" cy="12" rx="4.2" ry="9.5"/>
            <path d="M2.5 12h19M4 7h16M4 17h16"/>
          </svg>
          <span>www.<span class="web-domain">rollersandglides-demo</span>.com</span>
        </li>
      </ul>
    </div>
  </section>
</main>
</body>
</html>
```